VOMRA Pty Ltd Business Card

Looking for a simple yet eye-catching double-sided business card design using my company logo on one side and contact details on the other.

Target Market(s)

Government

Industry/Entity Type

Communication Systems Engineering

Contact Information for Business Card

VOMRA Pty Ltd

Requirements
Nice to have
• Would be great to have a QR code so details can be scanned into contacts

```html
<!DOCTYPE html>
<html lang="en">
<head>
<meta charset="utf-8">
<title>VOMRA Pty Ltd Business Card</title>
<link rel="stylesheet" href="https://fonts.googleapis.com/css2?family=Open+Sans:wght@400;600;700;800&display=swap">
<style>
  :root {
    --page: #e9e6e2;
    --card: #353f47;
    --card-deep: #2a3239;
    --ink-light: #ffffff;
    --ink-soft: #dfe4e8;
    --mark-dim: #242b31;
    --shadow: rgba(20, 24, 28, 0.28);
  }
  * { box-sizing: border-box; margin: 0; padding: 0; }
  html, body {
    width: 1200px; height: 780px; overflow: hidden;
    background: var(--page);
    font-family: "Open Sans", Arial, sans-serif;
  }
  .sheet {
    width: 1200px; height: 780px;
    display: flex; align-items: center; justify-content: center; gap: 44px;
  }
  .card {
    position: relative;
    width: 540px; height: 330px;
    background: var(--card);
    border-radius: 22px;
    box-shadow: 0 14px 30px var(--shadow);
    overflow: hidden;
    color: var(--ink-light);
  }
  /* Contact side */
  .brand {
    position: absolute; left: 34px; top: 34px;
    display: flex; align-items: center; gap: 12px;
  }
  .brand-dot {
    width: 22px; height: 22px; border-radius: 50%;
    background: var(--ink-light);
  }
  .brand-name {
    font-weight: 800; font-size: 40px; letter-spacing: 3px; line-height: 1;
    color: var(--ink-light);
  }
  .contact {
    position: absolute; left: 34px; top: 112px;
    font-size: 13px; line-height: 1.55; color: var(--ink-soft);
    list-style: none;
  }
  .contact .address { margin-bottom: 4px; }
  .contact li { display: flex; align-items: center; gap: 8px; }
  .contact svg { width: 12px; height: 12px; flex: none; fill: var(--ink-soft); }
  .person {
    position: absolute; right: 40px; top: 140px;
    text-align: right;
  }
  .person-name { font-weight: 700; font-size: 27px; line-height: 1.15; }
  .person-role { font-size: 15px; color: var(--ink-soft); margin-top: 2px; }
  .edge-bar {
    position: absolute; right: 0; top: 138px;
    width: 14px; height: 58px; background: var(--ink-light);
  }
  /* Logo side */
  .card--back { background: var(--card); }
  .back-brand {
    position: absolute; inset: 0;
    display: flex; align-items: center; justify-content: center; gap: 16px;
  }
  .back-brand .brand-dot { width: 30px; height: 30px; background: var(--mark-dim); }
  .back-brand .brand-name { font-size: 62px; letter-spacing: 5px; color: var(--mark-dim); }
</style>
</head>
<body>
<main class="sheet">
  <section class="card card--front" aria-label="Contact side">
    <div class="brand">
      <span class="brand-dot"></span>
      <span class="brand-name">VOMRA</span>
    </div>
    <ul class="contact">
      <li class="address">47-49 Harlow Lane Redfern<br>NSW 2016 Australia</li>
      <li><svg viewBox="0 0 24 24" aria-hidden="true"><path d="M6.6 10.8a15 15 0 0 0 6.6 6.6l2.2-2.2a1 1 0 0 1 1-.25 11.4 11.4 0 0 0 3.6.6 1 1 0 0 1 1 1V20a1 1 0 0 1-1 1A17 17 0 0 1 3 4a1 1 0 0 1 1-1h3.5a1 1 0 0 1 1 1c0 1.25.2 2.45.6 3.6a1 1 0 0 1-.25 1z"/></svg>(817) 555-0142</li>
      <li><svg viewBox="0 0 24 24" aria-hidden="true"><circle cx="12" cy="12" r="10"/></svg>www.vomra.com.au</li>
      <li><svg viewBox="0 0 24 24" aria-hidden="true"><path d="M2 5h20v14H2z M2 5l10 8 10-8" /></svg>admin@vomra.com.au</li>
    </ul>
    <div class="person">
      <p class="person-name">Jordan Mercer</p>
      <p class="person-role">Co-Founder</p>
    </div>
    <span class="edge-bar"></span>
  </section>

  <section class="card card--back" aria-label="Logo side">
    <div class="back-brand">
      <span class="brand-dot"></span>
      <span class="brand-name">VOMRA</span>
    </div>
  </section>
</main>
</body>
</html>
```